Tall Fern Roofing Business Card

Need a business card with the logo that was designed here

Contact Information for Business Card

Name, Title, Phone, Email, Website, Company name

```html
<!DOCTYPE html>
<html lang="en">
<head>
<meta charset="utf-8">
<title>Tall Fern Roofing Business Card</title>
<link href="https://fonts.googleapis.com/css2?family=Montserrat:wght@400;500;700&display=swap" rel="stylesheet">
<style>
  :root {
    --page: #ececec;
    --front-bg: #7f7e7f;
    --silver: #d4d4d4;
    --card-white: #ffffff;
    --brand-blue: #3f6fbf;
    --text-grey: #6a6a6a;
  }
  html, body {
    margin: 0;
    width: 1200px;
    height: 900px;
    overflow: hidden;
    background: var(--page);
    font-family: "Montserrat", sans-serif;
  }
  .canvas {
    position: relative;
    width: 1200px;
    height: 900px;
  }
  .card {
    position: absolute;
    left: 285px;
    width: 630px;
    height: 360px;
    box-shadow: 0 6px 18px rgba(0,0,0,0.12);
    box-sizing: border-box;
  }
  .card--front {
    top: 70px;
    background: var(--front-bg);
    display: flex;
    align-items: center;
    justify-content: center;
  }
  .card--back {
    top: 470px;
    background: var(--card-white);
    display: flex;
    align-items: center;
    padding: 0 40px 0 50px;
  }
  .wordmark {
    display: flex;
    align-items: center;
    gap: 12px;
    font-weight: 700;
    font-size: 30px;
    letter-spacing: 0.5px;
    white-space: nowrap;
  }
  .wordmark__square {
    width: 14px;
    height: 14px;
  }
  .card--front .wordmark { color: var(--silver); }
  .card--front .wordmark__square { background: var(--silver); }
  .card--back .wordmark { color: var(--brand-blue); font-size: 24px; }
  .card--back .wordmark__square { background: var(--brand-blue); width: 12px; height: 12px; }
  .divider {
    width: 1.5px;
    height: 200px;
    background: var(--brand-blue);
    margin: 0 30px 0 34px;
  }
  .contact { color: var(--text-grey); }
  .contact__name {
    margin: 0;
    color: var(--brand-blue);
    font-weight: 700;
    font-size: 22px;
    letter-spacing: 0.5px;
    text-transform: uppercase;
  }
  .contact__title {
    margin: 2px 0 14px;
    font-size: 14px;
  }
  .contact__list {
    list-style: none;
    margin: 0 0 12px;
    padding: 0;
    font-size: 14px;
    line-height: 24px;
  }
  .contact__list li { display: flex; align-items: center; gap: 8px; }
  .contact__icon { width: 12px; height: 12px; fill: var(--brand-blue); }
  .contact__address { margin: 0; font-size: 14px; line-height: 21px; font-style: normal; }
</style>
</head>
<body>
<main class="canvas">
  <section class="card card--front">
    <div class="wordmark"><span class="wordmark__square"></span>Tall Fern Roofing</div>
  </section>

  <section class="card card--back">
    <div class="wordmark"><span class="wordmark__square"></span>Tall Fern Roofing</div>
    <div class="divider"></div>
    <div class="contact">
      <h1 class="contact__name">Marcus Hollings</h1>
      <p class="contact__title">Managing Director</p>
      <ul class="contact__list">
        <li>
          <svg class="contact__icon" viewBox="0 0 24 24" aria-hidden="true"><path d="M6.6 10.8a15 15 0 0 0 6.6 6.6l2.2-2.2c.3-.3.7-.4 1-.2 1.1.4 2.3.6 3.6.6.6 0 1 .4 1 1V20c0 .6-.4 1-1 1A17 17 0 0 1 3 4c0-.6.4-1 1-1h3.5c.6 0 1 .4 1 1 0 1.3.2 2.5.6 3.6.1.3 0 .7-.2 1z"/></svg>
          0400 555 019
        </li>
        <li>
          <svg class="contact__icon" viewBox="0 0 24 24" aria-hidden="true"><path d="M2 5h20v14H2zm2 2v.5l8 5 8-5V7z"/></svg>
          info@tallfernroofing.com
        </li>
        <li>
          <svg class="contact__icon" viewBox="0 0 24 24" aria-hidden="true"><circle cx="12" cy="12" r="10"/></svg>
          www.tallfernroofing.com
        </li>
      </ul>
      <address class="contact__address">1450 W Harlow Street<br>Kestrel County Name 5231</address>
    </div>
  </section>
</main>
</body>
</html>
```